Investment company needing business card

We are wanting a business card which looks sharp and easy on the eye. We are thinking of having a business card with the logo embossed on it, to really make it stand out. We will only have a small amount of information of the business card, person's name, position, email address and phone number

Contact Information for Business Card

Danielle Frost
Executive Assistant
+64 21 473 5162
danielf@harwickpartners.co.nz

Requirements
Must have
• Embossed logo
Should not have
• Not to be busy

```html
<!DOCTYPE html>
<html lang="en">
<head>
<meta charset="utf-8">
<title>Harwick Partners – Business Card</title>
<link rel="stylesheet" href="https://fonts.googleapis.com/css2?family=Open+Sans:wght@400;600;700&display=swap">
<style>
  :root {
    --backdrop: #e6e3df;
    --card-white: #ffffff;
    --brand-green: #22b573;
    --ink-grey: #555555;
    --bar-grey: #666666;
    --shadow: rgba(60, 50, 40, 0.18);
  }
  * { box-sizing: border-box; margin: 0; padding: 0; }
  html, body {
    width: 1200px;
    height: 997px;
    overflow: hidden;
    background: var(--backdrop);
    font-family: "Open Sans", Arial, sans-serif;
  }
  .canvas {
    position: relative;
    width: 1200px;
    height: 997px;
  }
  .card {
    position: absolute;
    left: 300px;
    width: 600px;
    height: 343px;
    box-shadow: 0 6px 18px var(--shadow);
  }
  .card--front { top: 130px; background: var(--card-white); }
  .card--back {
    top: 523px;
    background: var(--brand-green);
    display: flex;
    align-items: center;
    justify-content: center;
  }

  .wordmark {
    display: flex;
    align-items: center;
    gap: 12px;
    font-weight: 700;
    text-transform: uppercase;
    letter-spacing: 1.5px;
    white-space: nowrap;
  }
  .wordmark__square { width: 30px; height: 30px; display: block; }
  .card--front .wordmark {
    position: absolute;
    top: 52px;
    right: 48px;
    font-size: 24px;
    color: var(--brand-green);
  }
  .card--front .wordmark__square { background: var(--brand-green); }
  .card--back .wordmark { font-size: 34px; color: var(--card-white); }
  .card--back .wordmark__square { width: 42px; height: 42px; background: var(--card-white); }

  .identity {
    position: absolute;
    left: 0;
    top: 140px;
    padding-left: 48px;
  }
  .accent-bar {
    position: absolute;
    left: 24px;
    width: 8px;
    background: var(--bar-grey);
  }
  .identity .accent-bar { top: 8px; height: 26px; }
  .identity__name {
    font-weight: 700;
    font-size: 16px;
    color: var(--brand-green);
    text-transform: uppercase;
    letter-spacing: 0.3px;
  }
  .identity__role {
    font-size: 13px;
    color: var(--ink-grey);
  }

  .contact {
    position: absolute;
    left: 0;
    bottom: 42px;
    padding-left: 48px;
    list-style: none;
  }
  .contact .accent-bar { top: 2px; height: 60px; }
  .contact__item {
    display: flex;
    align-items: center;
    gap: 7px;
    font-size: 14px;
    line-height: 21px;
    color: var(--ink-grey);
  }
  .contact__icon { width: 11px; height: 11px; flex: none; }
</style>
</head>
<body>
<main class="canvas">

  <section class="card card--front" aria-label="Business card front">
    <div class="wordmark">
      <span class="wordmark__square"></span>
      <span class="wordmark__name">Harwick Partners</span>
    </div>

    <div class="identity">
      <span class="accent-bar"></span>
      <p class="identity__name">Danielle Frost</p>
      <p class="identity__role">Executive Assistant</p>
    </div>

    <ul class="contact">
      <span class="accent-bar"></span>
      <li class="contact__item">
        <svg class="contact__icon" viewBox="0 0 24 24" aria-hidden="true"><path fill="#22b573" d="M6.6 10.8a15.5 15.5 0 0 0 6.6 6.6l2.2-2.2c.3-.3.7-.4 1-.2 1.1.4 2.3.6 3.6.6.6 0 1 .4 1 1V20c0 .6-.4 1-1 1A17 17 0 0 1 3 4c0-.6.4-1 1-1h3.5c.6 0 1 .4 1 1 0 1.3.2 2.5.6 3.6.1.3 0 .7-.2 1z"/></svg>
        <span>+64 21 473 5162</span>
      </li>
      <li class="contact__item">
        <svg class="contact__icon" viewBox="0 0 24 24" aria-hidden="true"><rect x="2" y="5" width="20" height="14" rx="1" fill="#22b573"/><path d="M2 6l10 7 10-7" fill="none" stroke="#fff" stroke-width="2"/></svg>
        <span>danielf@harwickpartners.co.nz</span>
      </li>
      <li class="contact__item">
        <svg class="contact__icon" viewBox="0 0 24 24" aria-hidden="true"><circle cx="12" cy="12" r="10" fill="#22b573"/><path d="M2 12h20M12 2c3 3 3 17 0 20M12 2c-3 3-3 17 0 20" fill="none" stroke="#fff" stroke-width="1.5"/></svg>
        <span>www.harwickpartners.co.nz</span>
      </li>
    </ul>
  </section>

  <section class="card card--back" aria-label="Business card back">
    <div class="wordmark">
      <span class="wordmark__square"></span>
      <span class="wordmark__name">Harwick Partners</span>
    </div>
  </section>

</main>
</body>
</html>
```